2022 Yearly Patron Drive (art gallery annual report)

6X9, 16-page brochure that serves both as an annual report for the previous year and gets mailed for an ask for donations. This must be done in InDesign and I will provide a template. I am also sending PDFs for the previous two years. Last year was pink and black, but I have recolored the logo purple this year.. so am open to whatever colors. I used last year's template to put in the new info. The theme for this year is Amazing - last year was Thriving. The font I chose for the front I do not want to use.. its just an example. All three pictures on the front don't have to be used.. just ideas.
Updates

I put three photos on the front page. It isn't necessary to use all of them, I thought there might be something there to use as part of the design

The current information is in the InDesign file, Calatalog Design.indd with the to Links Folders attached.

Target Market(s)

Donors

Industry/Entity Type

Art

Font styles to use
Sans Serif

Requirements
Must have
• InDesign
Nice to have
• A new look! Something different than 2021 an 2020 (PDFs included)

```html
<!DOCTYPE html>
<html lang="en">
<head>
<meta charset="UTF-8">
<title>Exhibitions — Yearly Patron Drive</title>
<link rel="stylesheet" href="https://fonts.googleapis.com/css2?family=League+Gothic&family=Open+Sans:wght@400;700&family=Playfair+Display:wght@600&display=swap">
<style>
  :root {
    --ink: #000000;
    --paper: #ffffff;
    --magenta: #cc3399;
    --orange: #ff7a1f;
    --slate: #3b3550;
    --wine: #7a2a45;
    --photo-gallery: linear-gradient(180deg, #2a2a2a 0%, #d9d9d6 30%, #c9c9c6 60%, #5a5856 100%);
    --photo-visitors: linear-gradient(180deg, #d8d8d4 0%, #c4c2bd 50%, #6e6a66 100%);
  }
  * { margin: 0; padding: 0; box-sizing: border-box; }
  html, body { width: 1200px; height: 800px; overflow: hidden; background: var(--paper); }
  .page {
    position: relative;
    width: 1200px;
    height: 800px;
    overflow: hidden;
    font-family: "Open Sans", sans-serif;
    color: var(--ink);
  }
  .swoosh { position: absolute; left: 0; top: 0; }
  .brand {
    position: absolute;
    left: 54px;
    top: 50px;
    font-family: "Open Sans", sans-serif;
    font-weight: 700;
    font-size: 30px;
    letter-spacing: 3px;
    color: var(--ink);
  }
  .feature {
    position: absolute;
    left: 0;
    top: 133px;
    width: 862px;
    height: 522px;
    background: var(--ink);
  }
  .feature-title {
    position: absolute;
    left: 113px;
    top: 18px;
    font-family: "League Gothic", sans-serif;
    font-weight: 400;
    font-size: 74px;
    line-height: 1;
    color: var(--orange);
  }
  .feature-body {
    position: absolute;
    left: 113px;
    top: 240px;
    width: 585px;
    font-size: 18px;
    letter-spacing: -0.3px;
    line-height: 24px;
    color: var(--paper);
  }
  .feature-body .line {
    display: block;
    white-space: nowrap;
    text-align: justify;
    text-align-last: justify;
  }
  .feature-body .line-end { text-align-last: left; }
  .photo { position: absolute; }
  .photo-gallery { left: 904px; top: 133px; width: 296px; height: 215px; background: var(--photo-gallery); }
  .photo-visitors { left: 931px; top: 442px; width: 269px; height: 217px; background: var(--photo-visitors); }
  .caption {
    position: absolute;
    font-size: 18.5px;
    white-space: nowrap;
    color: var(--ink);
  }
  .caption .dash { color: var(--magenta); font-weight: 700; margin-right: 4px; }
  .caption-gallery { left: 954px; top: 363px; }
  .caption-visitors { left: 931px; top: 667px; }
  .folio {
    position: absolute;
    left: 0;
    top: 739px;
    width: 55px;
    height: 25px;
    background: var(--slate);
    border-radius: 0 13px 13px 0;
    color: var(--paper);
    font-weight: 700;
    font-size: 14px;
    line-height: 25px;
    text-align: right;
    padding-right: 10px;
  }
  .theme {
    position: absolute;
    left: 67px;
    top: 734px;
    font-family: "Playfair Display", serif;
    font-weight: 600;
    font-size: 26px;
    color: var(--wine);
  }
  .rule {
    position: absolute;
    left: 189px;
    top: 754px;
    width: 1011px;
    height: 1px;
    background: var(--ink);
  }
</style>
</head>
<body>
<div class="page">
  <svg class="swoosh" width="1200" height="800" viewBox="0 0 1200 800" aria-hidden="true">
    <path d="M694 133 C730 95 755 50 760 0 L793 0 C792 45 788 95 780 133 Z" fill="var(--magenta)"/>
    <path d="M0 655 L306 655 C250 670 210 672 150 680 C100 687 40 690 0 684 Z" fill="var(--magenta)"/>
  </svg>

  <div class="brand">HALVERSEN</div>

  <section class="feature">
    <h1 class="feature-title">EXHIBITIONS</h1>
    <p class="feature-body">
      <span class="line">The exhibits each year at the Halversen Gallery provide not only an</span>
      <span class="line">insight into the artistic talents of local students and artists, but also</span>
      <span class="line">into the creativity and ideas of artists from around the world. The</span>
      <span class="line">spring exhibit is usually reserved for the School of Studio Arts</span>
      <span class="line">(SOSA) and fall highlights our Cascade Valley artists (CVAS).</span>
      <span class="line">The remaining exhibits focus on a single artist, group of artists, juried</span>
      <span class="line line-end">competitions such as the Open Lens Photography Showcase and</span>
      <span class="line line-end">a special Members’ Exhibition.</span>
    </p>
  </section>

  <div class="photo photo-gallery" role="img" aria-label="Gallery room with colourful circular paintings on white walls and a grey bench"></div>
  <p class="caption caption-gallery"><span class="dash">-</span>Circles of Stillness and Light</p>

  <div class="photo photo-visitors" role="img" aria-label="Visitors viewing framed prints in the gallery"></div>
  <p class="caption caption-visitors"><span class="dash">-</span>Marcus Delaney: 3 Series of Prints</p>

  <div class="folio">12</div>
  <div class="theme">Amazing</div>
  <div class="rule"></div>
</div>
</body>
</html>
```